Website design with eCommerce for revolutionary new product in the manufacturing industry.

We need a website designed for a precision manufacturing company based in the suburbs of Minneapolis, Minnesota called Velkrin Manufacturing. We have a revolutionary new product, the TARN LOCK, to introduce and sell through an eCommerce storefront. The website would include company information, product information, and the storefront. Green is a color that represents Velkrin Manufacturing. The final design should communicate that we exclusively offer premium products at a premium price. The design should also let the customer know they are the focus of our work.

Target Market(s)

Machinists and machine shops

Industry/Entity Type

Manufacturing and machine shops

Coding

Coded - Design and coding required

Font styles to use
Sans Serif

Colors
59FF00
82FF00
B8FF75
E3FFCB
F4FFEA

Requirements
Must have
• eCommerce storefront, Made in USA references
Nice to have
• Home page, TARN LOCK Product page, About Us, Capabilities, Contact, etc.
Should not have
• Should not be too much text and reading.

```html
<!DOCTYPE html>
<html lang="en">
<head>
<meta charset="utf-8">
<title>TARN LOCK – Product | Velkrin Manufacturing</title>
<link href="https://fonts.googleapis.com/css2?family=Poppins:ital,wght@0,400;0,500;0,600;0,700;0,800;1,800;1,900&display=swap" rel="stylesheet">
<style>
:root{
  --green:#59ff00;
  --green-2:#82ff00;
  --green-soft:#b8ff75;
  --product-green:#2fa51a;
  --product-green-dark:#1d6e10;
  --foam:#2a2a2a;
  --foam-dark:#1a1a1a;
  --ink:#111111;
  --white:#ffffff;
  --muted:#cfcfcf;
  --social:#1c1c1c;
}
*{margin:0;padding:0;box-sizing:border-box}
html,body{width:1200px;height:2265px;overflow:hidden}
body{position:relative;background:var(--white);font-family:'Poppins',sans-serif;color:var(--ink)}

/* hero */
.hero-shape{position:absolute;left:0;top:0;width:1200px;height:430px}
.nav{position:absolute;left:89px;top:24px;width:1020px;height:67px;background:var(--white);border-radius:8px;box-shadow:0 4px 18px rgba(0,0,0,.15);display:flex;align-items:center;padding:0 16px}
.brand{font-weight:800;font-size:20px;letter-spacing:1px;color:var(--ink);display:flex;align-items:center;gap:8px;width:184px}
.brand-square{width:12px;height:12px;background:var(--ink)}
.nav-links{display:flex;gap:15px;list-style:none;font-size:11px;font-weight:600;white-space:nowrap}
.nav-cta{margin-left:auto;background:var(--green);color:var(--ink);font-size:12px;font-weight:600;padding:10px 17px;border-radius:4px;transform:skewX(-4deg)}
.hero-title{position:absolute;left:0;width:1200px;top:183px;text-align:center;color:var(--white);font-size:49px;font-weight:900;font-style:italic;letter-spacing:1px}
.scroll-mouse{position:absolute;left:590px;top:298px}

/* products */
.product-card{position:absolute;top:518px;width:320px;height:357px;border-radius:16px;transform:skewX(-5deg);overflow:hidden;
  background:
    linear-gradient(115deg,transparent 55%,rgba(47,165,26,.55) 70%,rgba(47,165,26,.15) 82%,transparent 92%),
    linear-gradient(180deg,var(--foam) 0%,var(--foam-dark) 100%);
  box-shadow:inset 0 0 0 1px rgba(255,255,255,.04)}
.product-name{position:absolute;top:890px;width:240px;text-align:center;font-size:28px;font-weight:800;font-style:italic;letter-spacing:.5px}

/* info */
.info-visual{position:absolute;left:70px;top:1025px;width:440px;height:540px;border-radius:40px;transform:skewX(-6deg);
  background:linear-gradient(150deg,#3cc423 0%,var(--product-green) 45%,var(--product-green-dark) 100%);
  box-shadow:0 30px 60px rgba(0,0,0,.18)}
.info-title{position:absolute;left:601px;top:1040px;font-size:45px;font-weight:900;font-style:italic;letter-spacing:.5px}
.feature-list{position:absolute;left:601px;top:1108px;width:520px;list-style:none;font-size:12.7px;line-height:19.6px;color:var(--ink);white-space:nowrap}
.feature-list li{padding-left:15px;position:relative}
.feature-list li::before{content:"";position:absolute;left:1px;top:7px;width:6px;height:6px;border-radius:50%;background:var(--green)}
.feature-list li.sub{padding-left:57px}
.feature-list li.sub::before{left:30px;width:6px;height:6px;background:none;border:1.3px solid var(--green)}
.feature-list li.plain::before{display:none}

/* newsletter + footer */
.footer-shape{position:absolute;left:0;top:1730px;width:1200px;height:535px}
.news-shape{position:absolute;left:0;top:1655px;width:1200px;height:165px}
.news-title{position:absolute;left:168px;top:1694px;font-size:43px;font-weight:900;font-style:italic;letter-spacing:.5px}
.news-sub{position:absolute;left:164px;top:1748px;font-size:17px;font-weight:500}
.news-input{position:absolute;left:566px;top:1726px;font-size:16px;color:#777}
.news-btn{position:absolute;left:922px;top:1724px;font-size:17px;font-weight:800;color:var(--white);letter-spacing:.5px}

.footer-brand{position:absolute;left:87px;top:2014px;display:flex;align-items:center;gap:12px;color:var(--white);font-size:34px;font-weight:800;letter-spacing:1px}
.footer-brand .brand-square{width:18px;height:18px;background:var(--white)}
.footer-col{position:absolute;top:1947px}
.footer-col h3{color:var(--green);font-size:17px;font-weight:800;font-style:italic;margin-bottom:8px}
.footer-col ul{list-style:none;font-size:13.3px;line-height:21.4px;color:var(--muted)}
.contact-list li{display:flex;align-items:center;gap:7px}
.socials{position:absolute;left:857px;top:2000px;display:flex;gap:7px}
.social-btn{width:38px;height:38px;border-radius:50%;background:var(--social);display:flex;align-items:center;justify-content:center}
.divider{position:absolute;left:89px;top:2207px;width:1022px;height:1px;background:#333}
.copyright{position:absolute;left:0;width:1200px;top:2224px;text-align:center;color:var(--white);font-size:15px;font-weight:500}
.to-top{position:absolute;left:1129px;top:2190px;width:40px;height:40px;border-radius:50%;background:var(--green);display:flex;align-items:center;justify-content:center}
</style>
</head>
<body>

<header>
  <svg class="hero-shape" viewBox="0 0 1200 430" role="img" aria-label="Dark photo of stacked machined parts">
    <defs>
      <radialGradient id="heroTone" cx="50%" cy="40%" r="70%">
        <stop offset="0" stop-color="#3a3836"/>
        <stop offset="1" stop-color="#151413"/>
      </radialGradient>
    </defs>
    <path d="M0 0 H1200 V270 Q1192 415 1095 425 L620 380 L0 316 Z" fill="url(#heroTone)"/>
    <path d="M0 316 L640 379 L0 404 Z" fill="#59ff00"/>
  </svg>

  <nav class="nav">
    <div class="brand"><span class="brand-square"></span>TARN LOCK</div>
    <ul class="nav-links">
      <li>WHY VELKRIN MANUFACTURING?</li>
      <li>WHAT WE DO</li>
      <li>HOW WE MAKE IT BETTER</li>
      <li>CAPABILITIES</li>
      <li>GALLERY</li>
      <li>ABOUT US</li>
      <li>WISDOM</li>
    </ul>
    <div class="nav-cta">CONTACT</div>
  </nav>

  <h1 class="hero-title">PRODUCT</h1>
  <svg class="scroll-mouse" width="20" height="34" viewBox="0 0 20 34">
    <rect x="1.5" y="1.5" width="17" height="31" rx="8.5" fill="none" stroke="#fff" stroke-width="2"/>
    <line x1="10" y1="7" x2="10" y2="13" stroke="#fff" stroke-width="2" stroke-linecap="round"/>
  </svg>
</header>

<section class="products">
  <div class="product-card" style="left:105px" role="img" aria-label="TLK-001 kit: green stop arm, rods and hex key in foam case"></div>
  <div class="product-card" style="left:440px" role="img" aria-label="TLK-002 kit: green stop arm, rods and hex key in foam case"></div>
  <div class="product-card" style="left:773px" role="img" aria-label="TLK-003 kit: two green stop arms, rods and hex key in foam case"></div>
  <div class="product-name" style="left:128px">TLK-001</div>
  <div class="product-name" style="left:479px">TLK-002</div>
  <div class="product-name" style="left:797px">TLK-003</div>
</section>

<section class="info">
  <div class="info-visual" role="img" aria-label="Rendered green TARN LOCK stop arm with stop rod"></div>
  <h2 class="info-title">PRODUCT INFO</h2>
  <ul class="feature-list">
    <li>Fastest and most reliable setups</li>
    <li>The locating stop rod is the highest point, so cutting clearance is no<br>longer an issue</li>
    <li>The stop rod is top-loading</li>
    <li class="sub">No need to slide it the full length to replace it</li>
    <li>You can use a wide range of shapes and sizes of stop rods</li>
    <li class="sub" style="margin-top:4px">This means the end user can easily and quickly use<br>almost any item at hand</li>
    <li class="sub">No need for exact shape and size rods</li>
    <li style="margin-top:6px">The clamping mechanisms do not require material deformation to function</li>
    <li>The adjustment fasteners are visible and very easy to access for quick and<br>simple adjustments</li>
    <li>Only two fasteners are needed to access the full range of movements</li>
    <li>The arm can be rotated and adjusted without changing the X-axis location</li>
    <li>The system can be mounted to many different vises, the machine table or<br>fixture surface</li>
    <li>The design is modular to allow for easy customization or replacement</li>
    <li class="plain">Plenty of room for chip and coolant evacuation</li>
    <li>Inherently square to the workholding for intuitive adjustments</li>
    <li>Allows for use with very small, or very large parts, as well as oddly shaped parts</li>
    <li class="plain">Replacement parts are readily available</li>
    <li>The materials and fasteners are very common so maintenance is simple</li>
    <li class="plain">Made in USA</li>
  </ul>
</section>

<footer>
  <svg class="footer-shape" viewBox="0 0 1200 535">
    <path d="M0 114 L1085 5 Q1190 0 1200 140 V535 H0 Z" fill="#000"/>
  </svg>
  <svg class="news-shape" viewBox="0 0 1200 165">
    <path d="M130 5 H1098 Q1110 5 1106 18 L1080 140 Q1076 152 1062 152 H104 Q90 152 93 140 L116 18 Q119 5 130 5 Z" fill="#59ff00"/>
    <path d="M552 53 H890 L872 110 H546 Q536 110 538 100 L544 62 Q546 53 552 53 Z" fill="#fff"/>
    <path d="M893 53 H1055 Q1064 53 1061 62 L1052 101 Q1050 110 1040 110 H871 Z" fill="#111"/>
  </svg>
  <div class="news-title">NEWSLETTER</div>
  <div class="news-sub">Subscribe to our newsletter</div>
  <div class="news-input">Enter your email</div>
  <div class="news-btn">SUBSCRIBE</div>

  <div class="footer-brand"><span class="brand-square"></span>TARN LOCK</div>

  <div class="footer-col" style="left:377px">
    <h3>USEFUL LINKS</h3>
    <ul>
      <li>Why Velkrin Manufacturing?</li>
      <li>What we do</li>
      <li>How we make it better</li>
      <li>Capabilities</li>
      <li>About us</li>
      <li>Gallery</li>
      <li>Wisdom</li>
    </ul>
  </div>

  <div class="footer-col" style="left:606px">
    <h3>CONTACT US</h3>
    <ul class="contact-list">
      <li><svg width="10" height="12" viewBox="0 0 10 12"><path d="M5 0a4 4 0 0 1 4 4c0 3-4 8-4 8S1 7 1 4a4 4 0 0 1 4-4z" fill="#59ff00"/><circle cx="5" cy="4" r="1.5" fill="#000"/></svg>4180 Cedar Ridge Rd, Plymouth MN</li>
      <li><svg width="11" height="9" viewBox="0 0 11 9"><rect width="11" height="9" rx="1" fill="#59ff00"/><path d="M0 1 L5.5 5 L11 1" stroke="#000" fill="none"/></svg>hello@velkrinmfg.com</li>
      <li><svg width="11" height="11" viewBox="0 0 11 11"><path d="M2 0 L4 2.5 L3 4 Q4.5 6.5 7 8 L8.5 7 L11 9 L9.5 11 Q3 10 0 1.5 Z" fill="#59ff00"/></svg>+1 612 555 0148</li>
      <li><svg width="11" height="11" viewBox="0 0 11 11"><rect x="2" y="0" width="7" height="3" fill="#59ff00"/><rect x="0" y="3.5" width="11" height="5" rx="1" fill="#59ff00"/><rect x="2.5" y="7" width="6" height="4" fill="#59ff00" stroke="#000" stroke-width=".6"/></svg>+1 612 555 0149</li>
    </ul>
  </div>

  <div class="socials" aria-label="Contact shortcuts">
    <span class="social-btn"><svg width="14" height="14" viewBox="0 0 14 14"><circle cx="7" cy="7" r="5.5" fill="none" stroke="#fff" stroke-width="1.4"/><path d="M1.5 7 H12.5 M7 1.5 Q4 7 7 12.5 Q10 7 7 1.5" fill="none" stroke="#fff" stroke-width="1.2"/></svg></span>
    <span class="social-btn"><svg width="14" height="11" viewBox="0 0 14 11"><rect x=".7" y=".7" width="12.6" height="9.6" rx="1.2" fill="none" stroke="#fff" stroke-width="1.4"/><path d="M1 1.5 L7 6 L13 1.5" fill="none" stroke="#fff" stroke-width="1.3"/></svg></span>
    <span class="social-btn"><svg width="13" height="13" viewBox="0 0 11 11"><path d="M2 0 L4 2.5 L3 4 Q4.5 6.5 7 8 L8.5 7 L11 9 L9.5 11 Q3 10 0 1.5 Z" fill="#fff"/></svg></span>
    <span class="social-btn"><svg width="12" height="14" viewBox="0 0 10 12"><path d="M5 0a4 4 0 0 1 4 4c0 3-4 8-4 8S1 7 1 4a4 4 0 0 1 4-4z" fill="#fff"/><circle cx="5" cy="4" r="1.5" fill="#1c1c1c"/></svg></span>
  </div>

  <div class="divider"></div>
  <div class="copyright">©Copyright 2022 | All Rights Reserved</div>
  <div class="to-top">
    <svg width="10" height="6" viewBox="0 0 10 6"><path d="M1 5 L5 1 L9 5" stroke="#111" stroke-width="1.6" fill="none"/></svg>
  </div>
</footer>

</body>
</html>
```